Voltaro Cycles Company

I need a Voltaro Cycles site for pre-orders, 3-4 models, multiple colors per order. The bikes are electric bikes, company logo color scheme has red. Maybe a countdown to a date when pre-order will close. I also want to incorporate a deposit style system for the pre-order with the balance due on shipping.

```html
<!DOCTYPE html>
<html lang="en">
<head>
<meta charset="utf-8">
<title>Voltaro Cycles – Electric Bike Pre-Orders</title>
<link rel="stylesheet" href="https://fonts.googleapis.com/css2?family=Roboto:wght@400;500;700;900&display=swap">
<style>
:root{
  --red:#e02b2b;
  --ink:#111111;
  --text:#555555;
  --light:#f4f4f4;
  --grey:#8a8a8a;
  --dark:#111214;
  --white:#ffffff;
}
*{box-sizing:border-box;margin:0;padding:0}
html,body{width:1200px;height:4959px;overflow:hidden}
body{position:relative;background:var(--white);font-family:"Roboto",Arial,sans-serif;color:var(--ink)}
.abs{position:absolute}
.brand{display:flex;align-items:center;gap:10px;font-weight:900;font-size:25px;letter-spacing:.5px;color:var(--ink);white-space:nowrap}
.brand-mark{width:14px;height:14px;background:var(--red);display:block}
.brand-footer{color:var(--white)}
.nav{left:428px;top:52px;display:flex;gap:32px;font-size:13px;font-weight:700}
.nav .active{color:var(--red)}
.account{left:874px;top:50px;font-size:13px;font-weight:700;display:flex;align-items:center;gap:8px}
.cart{left:1015px;top:50px;font-size:13px;font-weight:700;display:flex;align-items:center;gap:8px;border-left:1px solid #ddd;padding-left:14px}
.hero{left:0;top:120px;width:1200px;height:722px;background:linear-gradient(180deg,#5c6472 0%,#8b7a66 30%,#c08a3e 55%,#7a4d1f 80%,#3a2a18 100%)}
.hero-title{left:0;top:228px;width:1200px;text-align:center;color:#fff;font-weight:900;font-size:34px;line-height:46px;letter-spacing:.5px}
.digit{width:56px;height:77px;top:337px;background:rgba(70,70,70,.75);border-radius:6px;color:#fff;font-size:52px;line-height:77px;text-align:center}
.unit{top:428px;width:118px;text-align:center;color:#e8e8e8;font-weight:700;font-size:18px}
.btn{background:var(--red);color:#fff;font-weight:700;font-size:13px;text-align:center}
.section-title{left:0;width:1200px;text-align:center;font-weight:900;font-size:38px;letter-spacing:.5px}
.section-title span{color:var(--red)}
.about-title{left:112px;top:940px;font-weight:900;font-size:38px}
.about-title span{color:var(--red)}
.about-text{left:112px;width:424px;font-size:14px;line-height:25.5px;color:var(--text)}
.photo{overflow:hidden}
.cat-label{position:absolute;left:0;right:0;bottom:22px;text-align:center;color:#fff;font-weight:700;font-size:17px}
.product{width:231px;height:274px;top:2652px;background:#ececec}
.heart{position:absolute;right:22px;bottom:22px;width:32px;height:32px;border-radius:50%;background:#fff;display:flex;align-items:center;justify-content:center}
.swatches{top:2946px;width:231px;display:flex;justify-content:center;gap:6px}
.swatches i{width:12px;height:12px;border-radius:50%;border:2px solid #ddd;display:block}
.p-name{top:2973px;width:231px;text-align:center;font-weight:700;font-size:18px}
.p-price{top:3000px;width:231px;text-align:center;color:var(--red);font-weight:700;font-size:15px}
.arrow{font-size:40px;line-height:40px}
.blog-card{width:285px;height:246px;top:3515px;background:#fff;box-shadow:0 4px 16px rgba(0,0,0,.06);padding:0 22px}
.blog-date{margin-top:25px;display:inline-block;background:#7d7d7d;color:#fff;font-size:11px;padding:8px 12px}
.blog-h{margin-top:22px;font-weight:700;font-size:15px;line-height:23px}
.blog-p{margin-top:10px;font-size:14px;line-height:25px;color:#777;text-align:justify}
.read{margin-top:8px;color:var(--red);font-weight:700;font-size:13px;text-decoration:underline}
.t-card{width:304px;height:301px;top:4164px;background:#fff;box-shadow:0 4px 18px rgba(0,0,0,.10);text-align:center;padding:60px 24px 0}
.t-avatar{position:absolute;left:50%;top:-42px;margin-left:-42px;width:84px;height:84px;border-radius:50%;border:4px solid #fff}
.t-name{font-weight:700;font-size:18px}
.t-stars{color:var(--red);font-size:13px;letter-spacing:2px;margin-top:4px}
.t-text{margin-top:10px;font-size:14px;line-height:26.5px;color:#666}
.footer-links{font-size:14px;color:#fff;line-height:35px}
.news-title{left:595px;top:4700px;color:#fff;font-weight:700;font-size:22px}
.contact{left:595px;top:4828px;color:#fff;font-size:13px;display:flex;align-items:center;gap:14px}
.pay{width:46px;height:28px;background:#e9e9e9;border-radius:3px}
</style>
</head>
<body>

<header>
  <div class="abs brand" style="left:112px;top:44px"><i class="brand-mark"></i>VOLTARO CYCLES</div>
  <nav class="abs nav">
    <span class="active">HOME</span><span>PRODUCTS</span><span>ABOUT</span><span>BLOG</span><span>CONTACT US</span>
  </nav>
  <div class="abs account">
    <svg width="15" height="15" viewBox="0 0 16 16"><circle cx="8" cy="8" r="7" fill="none" stroke="#e02b2b" stroke-width="1.6"/><circle cx="8" cy="6.5" r="2.5" fill="#e02b2b"/><path d="M3.5 13c1-2.5 8-2.5 9 0" fill="#e02b2b"/></svg>ACCOUNT
  </div>
  <div class="abs cart">
    <svg width="17" height="15" viewBox="0 0 18 16"><path d="M1 2h3l2 8h9l2-6H5" fill="none" stroke="#e02b2b" stroke-width="1.8"/><circle cx="7" cy="13.5" r="1.5" fill="#e02b2b"/><circle cx="14" cy="13.5" r="1.5" fill="#e02b2b"/></svg>Cart(0)
  </div>
</header>

<section class="hero-section">
  <div class="abs hero" role="img" aria-label="Photo of three cyclists riding e-bikes across a hillside at sunset"></div>
  <svg class="abs" style="left:0;top:636px" width="1200" height="210"><polygon points="0,206 1200,0 1200,210 0,210" fill="#fff"/></svg>
  <h1 class="abs hero-title">RESERVE THE PRODUCT WITH INTIAL<br>PAYMENT OF 10%</h1>
  <div class="abs digit" style="left:331px">0</div><div class="abs digit" style="left:392px">0</div>
  <div class="abs digit" style="left:472px">0</div><div class="abs digit" style="left:533px">0</div>
  <div class="abs digit" style="left:612px">0</div><div class="abs digit" style="left:674px">0</div>
  <div class="abs digit" style="left:753px">0</div><div class="abs digit" style="left:815px">0</div>
  <div class="abs unit" style="left:331px">DAYS</div>
  <div class="abs unit" style="left:472px">HOURS</div>
  <div class="abs unit" style="left:612px">MINUTES</div>
  <div class="abs unit" style="left:753px">SECONDS</div>
  <div class="abs btn" style="left:541px;top:472px;width:118px;height:40px;line-height:40px">PRE-ORDER</div>
</section>

<section class="about">
  <h2 class="abs about-title">ABOUT <span>US</span></h2>
  <p class="abs about-text" style="top:1008px">Lorem ipsum dolor sit amet, consectetur adipiscing elit, sed do eiusmod tempor incididunt ut labore et dolore magna aliqua. Ut enim ad minim veniam, quis nostrud exercitation ullamco laboris nisi ut aliquip ex ea commodo consequat duis aute irure dolor in reprehenderit in voluptatea.</p>
  <p class="abs about-text" style="top:1150px">Lorem ipsum dolor sit amet, consectetur adipiscing elit, sed do eiusmod tempor incididunt ut labore et dolore magna aliqua ut enim ad minim veniamea.</p>
  <div class="abs btn" style="left:112px;top:1264px;width:132px;height:42px;line-height:42px">LEARN MORE</div>
  <svg class="abs" style="left:599px;top:878px" width="490" height="497" role="img" aria-label="Photo of a woman riding an e-bike on a mountain trail">
    <defs><linearGradient id="hexFill" x1="0" y1="0" x2="0" y2="1"><stop offset="0" stop-color="#6f9bd0"/><stop offset=".45" stop-color="#b9c7cf"/><stop offset=".7" stop-color="#7c8a5e"/><stop offset="1" stop-color="#5f6b45"/></linearGradient></defs>
    <polygon points="245,0 490,124 490,373 245,497 0,373 0,124" fill="url(#hexFill)"/>
  </svg>
</section>

<section class="categories">
  <div class="abs" style="left:0;top:1431px;width:1200px;height:900px;background:var(--light)"></div>
  <svg class="abs" style="left:0;top:1431px" width="1200" height="180"><polygon points="0,0 1200,0 597,88" fill="#fff"/><polygon points="0,0 597,88 0,179" fill="#e02b2b"/></svg>
  <h2 class="abs section-title" style="top:1627px">PRODUCT <span>CATEGORIES</span></h2>
  <div class="abs photo" style="left:112px;top:1722px;width:375px;height:518px;background:linear-gradient(180deg,#a9c3d8,#6f8d5a 45%,#4f6a36)" role="img" aria-label="Photo of a rider with an e-bike in alpine meadows"><div class="cat-label">LOREM IPSUM DOLOR</div></div>
  <div class="abs photo" style="left:503px;top:1722px;width:285px;height:250px;background:linear-gradient(180deg,#b8c4cc,#7b8a78 50%,#8a7f6a)" role="img" aria-label="Photo of a cyclist on a rocky mountain path"><div class="cat-label">LOREM IPSUM DOLOR</div></div>
  <div class="abs photo" style="left:801px;top:1722px;width:287px;height:250px;background:linear-gradient(180deg,#9bb4c8,#d7a85a 55%,#3c3a34)" role="img" aria-label="Photo of e-bike handlebars at sunset"><div class="cat-label">LOREM IPSUM DOLOR</div></div>
  <div class="abs photo" style="left:503px;top:1990px;width:585px;height:250px;background:linear-gradient(180deg,#a5bccd,#7e9470 45%,#5f7a45)" role="img" aria-label="Photo of an e-bike parked by a mountain lake"><div class="cat-label">LOREM IPSUM DOLOR</div></div>
  <svg class="abs" style="left:0;top:2330px" width="1200" height="184"><polygon points="0,0 1200,91 1200,184 0,184" fill="#fff"/><polygon points="0,0 597,91 0,91" fill="#f4f4f4"/><polygon points="597,91 1200,0 1200,183" fill="#8a8a8a"/></svg>
</section>

<section class="featured">
  <h2 class="abs section-title" style="top:2559px">FEATURED <span>PRODUCTS</span></h2>
  <div class="abs arrow" style="left:48px;top:2769px;color:#bbb">&#8249;</div>
  <div class="abs arrow" style="left:1126px;top:2769px">&#8250;</div>

  <div class="abs product" style="left:112px" role="img" aria-label="Photo of a black e-bike"><div class="heart"><svg width="14" height="13" viewBox="0 0 14 13"><path d="M7 12S1 8 1 4.3A3 3 0 0 1 7 3a3 3 0 0 1 6 1.3C13 8 7 12 7 12z" fill="none" stroke="#e02b2b" stroke-width="1.4"/></svg></div></div>
  <div class="abs product" style="left:361px" role="img" aria-label="Photo of a black and red e-bike"><div class="heart"><svg width="14" height="13" viewBox="0 0 14 13"><path d="M7 12S1 8 1 4.3A3 3 0 0 1 7 3a3 3 0 0 1 6 1.3C13 8 7 12 7 12z" fill="none" stroke="#e02b2b" stroke-width="1.4"/></svg></div></div>
  <div class="abs product" style="left:609px" role="img" aria-label="Photo of a yellow e-bike"><div class="heart"><svg width="14" height="13" viewBox="0 0 14 13"><path d="M7 12S1 8 1 4.3A3 3 0 0 1 7 3a3 3 0 0 1 6 1.3C13 8 7 12 7 12z" fill="none" stroke="#e02b2b" stroke-width="1.4"/></svg></div></div>
  <div class="abs product" style="left:857px" role="img" aria-label="Photo of a blue e-bike"><div class="heart"><svg width="14" height="13" viewBox="0 0 14 13"><path d="M7 12S1 8 1 4.3A3 3 0 0 1 7 3a3 3 0 0 1 6 1.3C13 8 7 12 7 12z" fill="none" stroke="#e02b2b" stroke-width="1.4"/></svg></div></div>

  <div class="abs swatches" style="left:112px"><i style="background:#222"></i><i style="background:#2b46a8"></i><i style="background:#e02b2b"></i><i style="background:#f2c21b"></i></div>
  <div class="abs swatches" style="left:361px"><i style="background:#222"></i><i style="background:#2b46a8"></i><i style="background:#e02b2b"></i><i style="background:#f2c21b"></i></div>
  <div class="abs swatches" style="left:609px"><i style="background:#222"></i><i style="background:#2b46a8"></i><i style="background:#e02b2b"></i><i style="background:#f2c21b"></i></div>
  <div class="abs swatches" style="left:857px"><i style="background:#222"></i><i style="background:#2b46a8"></i><i style="background:#e02b2b"></i><i style="background:#f2c21b"></i></div>

  <div class="abs p-name" style="left:112px">LOREM IPSUM DOL</div><div class="abs p-price" style="left:112px">$49.99</div>
  <div class="abs p-name" style="left:361px">LOREM IPSUM DOL</div><div class="abs p-price" style="left:361px">$49.99</div>
  <div class="abs p-name" style="left:609px">LOREM IPSUM DOL</div><div class="abs p-price" style="left:609px">$49.99</div>
  <div class="abs p-name" style="left:857px">LOREM IPSUM DOL</div><div class="abs p-price" style="left:857px">$49.99</div>
</section>

<section class="blog">
  <div class="abs" style="left:0;top:3062px;width:1200px;height:860px;background:var(--light)"></div>
  <svg class="abs" style="left:0;top:3062px" width="1200" height="180"><polygon points="0,0 1200,0 597,88" fill="#fff"/><polygon points="0,0 597,88 0,179" fill="#e02b2b"/></svg>
  <h2 class="abs section-title" style="top:3243px">LATEST <span>BLOG</span></h2>

  <div class="abs" style="left:112px;top:3326px;width:308px;height:214px;border-radius:6px;background:linear-gradient(180deg,#e3b36a,#a8703a 55%,#3b3a38)" role="img" aria-label="Photo of e-bikes at a charging station at sunset"></div>
  <div class="abs" style="left:446px;top:3326px;width:308px;height:214px;border-radius:6px;background:linear-gradient(180deg,#c9d9c2,#8fae7a 55%,#6b7a66)" role="img" aria-label="Photo of a man with a teal e-bike in a park"></div>
  <div class="abs" style="left:780px;top:3326px;width:308px;height:214px;border-radius:6px;background:linear-gradient(180deg,#d9dfe4,#9fb58c 55%,#4f5a4a)" role="img" aria-label="Photo of an e-bike plugged into a charger"></div>

  <article class="abs blog-card" style="left:123px"><span class="blog-date">&#9638; 23 OCT 2023</span><h3 class="blog-h">LOREM IPSUM DOLOR SIT CONSECTETUR</h3><p class="blog-p">Lorem ipsum dolor sit amet, con sectetur adipiscing elit, sed do eiusmod tempor.</p><div class="read">READ MORE</div></article>
  <article class="abs blog-card" style="left:457px"><span class="blog-date">&#9638; 23 OCT 2023</span><h3 class="blog-h">LOREM IPSUM DOLOR SIT CONSECTETUR</h3><p class="blog-p">Lorem ipsum dolor sit amet, con sectetur adipiscing elit, sed do eiusmod tempor.</p><div class="read">READ MORE</div></article>
  <article class="abs blog-card" style="left:791px"><span class="blog-date">&#9638; 23 OCT 2023</span><h3 class="blog-h">LOREM IPSUM DOLOR SIT CONSECTETUR</h3><p class="blog-p">Lorem ipsum dolor sit amet, con sectetur adipiscing elit, sed do eiusmod tempor.</p><div class="read">READ MORE</div></article>

  <svg class="abs" style="left:0;top:3833px" width="1200" height="184"><polygon points="0,0 1200,0 1200,184 0,184" fill="#fff"/><polygon points="0,0 1200,0 597,91" fill="#f4f4f4"/><polygon points="597,91 1200,0 1200,183" fill="#8a8a8a"/></svg>
</section>

<section class="testimonials">
  <h2 class="abs section-title" style="top:4036px">TESTIMONIALS</h2>
  <div class="abs arrow" style="left:48px;top:4290px;color:#bbb">&#8249;</div>
  <div class="abs arrow" style="left:1126px;top:4290px">&#8250;</div>

  <article class="abs t-card" style="left:112px"><div class="t-avatar" style="background:#9fb2c4" role="img" aria-label="Customer portrait"></div><div class="t-name">JOHN SMITH</div><div class="t-stars">&#9733;&#9733;&#9733;&#9733;&#9733;</div><p class="t-text">Lorem ipsum dolor sit amet, consec te adipiscing elit, sed do eiusmod tem por incididunt ut labore et dolore mag na aliqua. Ut enim ad minim veniam, quis nostrud exercitation ullamco laborisea.</p></article>
  <article class="abs t-card" style="left:448px"><div class="t-avatar" style="background:#c9c9c9" role="img" aria-label="Customer portrait"></div><div class="t-name">JOHN SMITH</div><div class="t-stars">&#9733;&#9733;&#9733;&#9733;&#9733;</div><p class="t-text">Lorem ipsum dolor sit amet, consec te adipiscing elit, sed do eiusmod tem por incididunt ut labore et dolore mag na aliqua. Ut enim ad minim veniam, quis nostrud exercitation ullamco laborisea.</p></article>
  <article class="abs t-card" style="left:784px"><div class="t-avatar" style="background:#e59a5c" role="img" aria-label="Customer portrait"></div><div class="t-name">JOHN SMITH</div><div class="t-stars">&#9733;&#9733;&#9733;&#9733;&#9733;</div><p class="t-text">Lorem ipsum dolor sit amet, consec te adipiscing elit, sed do eiusmod tem por incididunt ut labore et dolore mag na aliqua. Ut enim ad minim veniam, quis nostrud exercitation ullamco laborisea.</p></article>
</section>

<footer>
  <svg class="abs" style="left:0;top:4526px" width="1200" height="433"><polygon points="0,0 1200,125 1200,433 0,433" fill="#111214"/></svg>
  <div class="abs brand brand-footer" style="left:112px;top:4697px"><i class="brand-mark"></i>VOLTARO CYCLES</div>
  <div class="abs footer-links" style="left:112px;top:4750px">Home<br>Products<br>About<br>Blog</div>
  <div class="abs footer-links" style="left:334px;top:4750px">Privacy Policy<br>Shipping &amp; Returns<br>Contact Us</div>
  <div class="abs news-title">JOIN OUR NEWSLETTER</div>
  <div class="abs" style="left:595px;top:4762px;width:300px;border-bottom:1px solid #666;color:#ddd;font-size:13px;padding-bottom:12px">Enter Your Email Here</div>
  <div class="abs btn" style="left:930px;top:4748px;width:137px;height:48px;line-height:48px;font-size:15px">SUBSCRIBE</div>
  <div class="abs contact">
    <span style="color:#e02b2b">&#9990;</span><span>+1 (555) 010 2030</span><span style="color:#888">|</span>
    <span style="color:#e02b2b">&#9993;</span><span>info@voltarocycles.example</span><span style="color:#888">|</span>
    <span style="display:flex;gap:10px"><i style="width:10px;height:10px;border-radius:50%;background:#fff;display:block"></i><i style="width:10px;height:10px;border-radius:50%;background:#fff;display:block"></i><i style="width:10px;height:10px;border-radius:50%;background:#fff;display:block"></i></span>
  </div>
  <div class="abs" style="left:112px;top:4894px;width:976px;border-top:1px solid #444"></div>
  <div class="abs" style="left:112px;top:4916px;color:#fff;font-size:11px">© 2023 VOLTARO CYCLES &nbsp;|&nbsp; All Rights Reserved</div>
  <div class="abs" style="left:838px;top:4907px;display:flex;gap:5px"><i class="pay"></i><i class="pay"></i><i class="pay"></i><i class="pay"></i><i class="pay"></i></div>
</footer>

</body>
</html>
```